Finding the Root: Reason in Clinical Choice-Crafting

I'd like a cover that looks like it would fit on the shelf next to "The Illness Mirage" by Corwin Talley, "The Close of Forgetting" by Hugh Marchetti, "Meal Mend" by Paul Grieve, "The Energy Restart Plan" by Oscar Pemberley or "The Gland Restart Plan" by the same or "The Cortex Restart Plan" by the same ... either text only (with some interesting fonts that make the title stand out, and the subtitle smaller) or a relevant image, though I'm not entirely sure what that would be since this is a book about big-picture medical decision making.
Author name is Dr Tessa Morrow, NMD
I'll eventually request an e-book, paperback, and audio cover from the winner...

Target Market(s)

practicing physicians

Industry/Entity Type

medicine

Requirements
Must have
• look similar to other books in the genre

```html
<!DOCTYPE html>
<html lang="en">
<head>
<meta charset="utf-8">
<title>Finding the Root: Reason in Clinical Choice-Crafting</title>
<link rel="stylesheet" href="https://fonts.googleapis.com/css2?family=Oswald:wght@300;500;700&family=Poppins:wght@400&display=swap">
<style>
  :root {
    --stage: #5b5b5b;
    --navy: #062a47;
    --blue: #0068a8;
    --sky: #d6eaf8;
    --white: #ffffff;
    --heart-red: #d60000;
    --heart-dark: #8f0000;
  }
  html, body {
    margin: 0;
    padding: 0;
    width: 673px;
    height: 1200px;
    overflow: hidden;
    background: var(--stage);
  }
  .book-cover {
    position: absolute;
    left: 26px;
    top: 136px;
    width: 620px;
    height: 928px;
    box-shadow: 0 10px 30px rgba(0,0,0,0.35);
  }
  .book-cover svg { display: block; }
  .series-line {
    font-family: "Poppins", sans-serif;
    font-weight: 400;
    font-size: 27px;
    letter-spacing: 8px;
    fill: var(--navy);
  }
  .title-small {
    font-family: "Oswald", sans-serif;
    font-weight: 700;
    fill: var(--navy);
  }
  .title-key {
    font-family: "Oswald", sans-serif;
    font-weight: 700;
    fill: var(--blue);
  }
  .author-name {
    font-family: "Oswald", sans-serif;
    font-weight: 500;
    font-size: 34px;
    letter-spacing: 6px;
    fill: var(--white);
  }
  .author-degree {
    font-weight: 300;
    letter-spacing: 4px;
  }
</style>
</head>
<body>
<div class="book-cover">
  <svg width="620" height="928" viewBox="0 0 620 928" xmlns="http://www.w3.org/2000/svg">
    <defs>
      <radialGradient id="coverGlow" cx="50%" cy="55%" r="65%">
        <stop offset="0.45" stop-color="#ffffff"/>
        <stop offset="1" stop-color="#cfe5f6"/>
      </radialGradient>
      <radialGradient id="heartTone" cx="40%" cy="30%" r="75%">
        <stop offset="0" stop-color="#ff2a1a"/>
        <stop offset="0.6" stop-color="#d60000"/>
        <stop offset="1" stop-color="#8f0000"/>
      </radialGradient>
      <radialGradient id="heartShadow" cx="50%" cy="50%" r="50%">
        <stop offset="0" stop-color="#000" stop-opacity="0.25"/>
        <stop offset="1" stop-color="#000" stop-opacity="0"/>
      </radialGradient>
    </defs>

    <rect class="cover-field" width="620" height="928" fill="url(#coverGlow)"/>

    <g class="title-block" text-anchor="middle">
      <text class="series-line" x="310" y="90">FINDING THE ROOT</text>
      <text class="title-small" x="310" y="176" font-size="88" textLength="250" lengthAdjust="spacingAndGlyphs">REASON IN</text>
      <text class="title-key" x="310" y="321" font-size="168" textLength="511" lengthAdjust="spacingAndGlyphs">CLINICAL</text>
      <text class="title-small" x="310" y="403" font-size="90" textLength="511" lengthAdjust="spacingAndGlyphs">CHOICE-CRAFTING</text>
    </g>

    <ellipse class="heart-shadow" cx="308" cy="728" rx="120" ry="14" fill="url(#heartShadow)"/>
    <rect class="heart-art" x="172" y="489" width="272" height="240" rx="110"
          fill="url(#heartTone)" role="img"
          aria-label="Glossy red heart illustration with a white heartbeat line across it"/>

    <g class="plus-icons" fill="none">
      <path class="plus-solid" d="M446 475h8v-12h14v12h12v14h-12v12h-14v-12h-8z" fill="var(--blue)" transform="translate(0 14) scale(1) translate(-8 -16)"/>
      <path class="plus-outline-small" d="M478 452h5v-5h6v5h5v6h-5v5h-6v-5h-5z" stroke="var(--blue)" stroke-width="1.5"/>
      <path class="plus-outline" d="M128 676h20v-20h22v20h20v22h-20v20h-22v-20h-20z" transform="translate(-5 -13) scale(1)" stroke="var(--blue)" stroke-width="2"/>
    </g>

    <rect class="author-rule" x="0" y="810" width="620" height="5" fill="var(--white)"/>
    <rect class="author-band" x="0" y="815" width="620" height="113" fill="var(--navy)"/>
    <text class="author-name" x="310" y="882" text-anchor="middle">DR TESSA MORROW, <tspan class="author-degree">NMD</tspan></text>
  </svg>
</div>
</body>
</html>
```